Business Card and Letterhead Design Project

We need a business card template and letterhead designed for our new business.
Business Card
The information on the business card will be:
Logo
"slogan" - A simple path to saving
Person's Name
Title
Phone Number
Email Address
Website
We strive to make everything SIMPLE so please keep that in mind.
If you want to design something that would go on an odd shaped business card, that is fine, we are up for any ideas.
The Letterhead would have:
logo
business address
phone
fax
website
Here is a link to our logo files: http://qlnk.example/8rTw2Vp
we can provide the winning designer with higher quality files if needbe.

```html
<!DOCTYPE html>
<html lang="en">
<head>
<meta charset="utf-8">
<title>Sproutvest Business Card</title>
<link href="https://fonts.googleapis.com/css2?family=Jost:wght@400;500;600&display=swap" rel="stylesheet">
<style>
  :root {
    --green: #7cb342;
    --white: #ffffff;
    --ink: #3a3a3a;
    --grey: #c9c9c9;
    --dark-rule: #3b3f45;
    --stage: #efefed;
  }
  * { box-sizing: border-box; margin: 0; padding: 0; }
  html, body { width: 1200px; height: 720px; overflow: hidden; }
  body {
    background: var(--stage);
    font-family: "Jost", "Futura", sans-serif;
    position: relative;
  }
  .card {
    position: absolute;
    top: 205px;
    width: 540px;
    height: 309px;
    overflow: hidden;
    box-shadow: 0 2px 8px rgba(0,0,0,0.15);
  }
  .card-front { left: 40px; background: var(--white); }
  .brand-block {
    position: absolute;
    left: 0; top: 0;
    width: 230px; height: 250px;
    display: flex; align-items: center; justify-content: center; gap: 10px;
  }
  .brand-dot {
    width: 18px; height: 18px; border-radius: 50%;
    background: var(--green);
  }
  .brand-name {
    color: var(--green);
    font-weight: 600;
    font-size: 28px;
  }
  .divider {
    position: absolute;
    left: 236px; top: 48px;
    width: 1px; height: 150px;
    background: var(--grey);
  }
  .contact {
    position: absolute;
    left: 262px; top: 48px;
    color: var(--ink);
  }
  .person-name {
    color: var(--green);
    font-weight: 600;
    font-size: 21px;
    line-height: 1.1;
  }
  .person-title { font-size: 13px; margin-top: 3px; margin-bottom: 14px; }
  .contact-line {
    display: flex; align-items: center; gap: 9px;
    font-size: 15px; margin-bottom: 7px;
  }
  .contact-line svg { width: 13px; height: 13px; flex: none; }
  .slogan-band { position: absolute; left: 0; bottom: 0; width: 540px; height: 90px; }
  .slogan {
    position: absolute;
    right: 18px; bottom: 34px;
    color: var(--white);
    font-size: 15px;
    letter-spacing: 0.04em;
  }
  .card-back {
    left: 620px;
    background: var(--green);
    display: flex; flex-direction: column; align-items: center; justify-content: center;
  }
  .back-brand {
    display: flex; align-items: center; gap: 14px;
    margin-top: 20px;
  }
  .back-brand .brand-dot { background: var(--white); width: 24px; height: 24px; }
  .back-brand .brand-name { color: var(--white); font-size: 40px; }
  .back-url {
    margin-top: 70px;
    color: var(--white);
    font-size: 15px;
    letter-spacing: 0.18em;
  }
</style>
</head>
<body>
  <section class="card card-front">
    <div class="brand-block">
      <span class="brand-dot"></span>
      <span class="brand-name">Sproutvest</span>
    </div>
    <div class="divider"></div>
    <div class="contact">
      <p class="person-name">Person’s Name</p>
      <p class="person-title">Title</p>
      <p class="contact-line">
        <svg viewBox="0 0 16 16" aria-hidden="true"><circle cx="8" cy="8" r="7" fill="none" stroke="#7cb342" stroke-width="1.6"/><path d="M5.5 4.5l1.5 1.5-1 1.2a6 6 0 0 0 2.8 2.8l1.2-1 1.5 1.5-1 1.2c-3 0-6.2-3.2-6.2-6.2z" fill="#7cb342"/></svg>
        123-456-7890
      </p>
      <p class="contact-line">
        <svg viewBox="0 0 16 16" aria-hidden="true"><rect x="1" y="3.5" width="14" height="9" rx="1" fill="#7cb342"/><path d="M1.5 4l6.5 5 6.5-5" fill="none" stroke="#fff" stroke-width="1.2"/></svg>
        info@sproutvest.example
      </p>
      <p class="contact-line">
        <svg viewBox="0 0 16 16" aria-hidden="true"><circle cx="8" cy="8" r="6.5" fill="none" stroke="#7cb342" stroke-width="1.5"/><ellipse cx="8" cy="8" rx="2.8" ry="6.5" fill="none" stroke="#7cb342" stroke-width="1.2"/><path d="M1.5 8h13" stroke="#7cb342" stroke-width="1.2"/></svg>
        www.sproutvest.example
      </p>
    </div>
    <svg class="slogan-band" viewBox="0 0 540 90" aria-hidden="true">
      <path d="M0 62 H250 C262 62 262 28 290 28 H540 V84 H0 Z" fill="#7cb342"/>
      <rect x="0" y="84" width="540" height="6" fill="#3b3f45"/>
    </svg>
    <p class="slogan">A simple path to saving</p>
  </section>

  <section class="card card-back">
    <div class="back-brand">
      <span class="brand-dot"></span>
      <span class="brand-name">Sproutvest</span>
    </div>
    <p class="back-url">www.sproutvest.example</p>
  </section>
</body>
</html>
```